Automotive component supplier needs a business card design

We need a business card design for our company called Velran Global Components Ltd based in the UK. We are a supplier of interior and exterior components to premium car manufacturers such as Corvel Ashby, Hadley Fenn, Marquist and Tavarelli. We would like to see a modern business card design that uses the colour blue.

Target Market(s)

Premium automotive car manufacturers.

Industry/Entity Type

Automotive

Contact Information for Business Card

Company Name : Velran Global Components Limited
Address: 17 Marlow Yard, Upper Heath, Warwick, CV31 8QL, United Kingdom
Web Address : www.velrancomponents-example.co.uk

Font styles to use
Other font styles liked:
• Helvetica

Colors
3176b5
0255a3
85acd3
cfdeed
cee9f5
85cae6
34a6d7
0692cd
9bcb3c

Requirements
Must have
• Clear company logo and a mixture of blue colours.
Nice to have
• A high quality modern image.
Should not have
• Multiple colours.

```html
<!DOCTYPE html>
<html lang="en">
<head>
<meta charset="utf-8">
<title>Velran Global Components – Business Card</title>
<link rel="stylesheet" href="https://fonts.googleapis.com/css2?family=Arimo:wght@400;700&display=swap">
<style>
  :root {
    --blue-main: #0692cd;
    --blue-deep: #0255a3;
    --blue-mid: #34a6d7;
    --blue-light: #85cae6;
    --green: #9bcb3c;
    --white: #ffffff;
    --stage: #e9eef3;
  }
  * { box-sizing: border-box; margin: 0; padding: 0; }
  html, body { width: 1200px; height: 950px; overflow: hidden; }
  body {
    background: var(--stage);
    font-family: "Arimo", Helvetica, Arial, sans-serif;
    position: relative;
  }
  .card {
    position: absolute;
    top: 325px;
    width: 520px;
    height: 300px;
    border-radius: 6px;
    overflow: hidden;
    box-shadow: 0 6px 18px rgba(2, 85, 163, 0.18);
  }

  /* Front */
  .card-front { left: 40px; background: var(--white); }
  .accent-strip {
    position: absolute; right: 0; top: 0;
    width: 16px; height: 100%;
    background: var(--green);
  }
  .front-brand {
    position: absolute; right: 44px; top: 26px;
    color: var(--blue-main);
    font-weight: 700;
    text-align: left;
  }
  .brand-name { display: block; font-size: 48px; letter-spacing: 1px; line-height: 1; }
  .brand-sub { display: block; font-size: 12px; letter-spacing: 1.2px; margin-top: 5px; white-space: nowrap; }

  .contact-panel {
    position: absolute; left: 0; bottom: 0;
    width: 318px; height: 190px;
    background: linear-gradient(160deg, var(--blue-mid), var(--blue-main));
    border-top-right-radius: 22px;
    color: var(--white);
    padding: 17px 0 0 28px;
  }
  .person-name { font-size: 19px; font-weight: 700; letter-spacing: 0.5px; }
  .person-role { font-size: 12.5px; margin: 2px 0 7px; }
  .address { font-size: 11.5px; line-height: 1.4; margin-bottom: 5px; }
  .contact-list { list-style: none; font-size: 11.5px; line-height: 1.5; }
  .contact-list li { display: flex; align-items: center; gap: 7px; }
  .contact-list svg { width: 11px; height: 11px; flex: none; }

  /* Back */
  .card-back { left: 640px; background: var(--blue-main); }
  .back-brand {
    position: absolute; left: 0; right: 0; top: 84px;
    text-align: center;
    color: var(--white);
    font-weight: 700;
  }
  .back-brand .brand-name { font-size: 82px; letter-spacing: 2px; }
  .back-brand .brand-sub { font-size: 17px; letter-spacing: 2px; margin-top: 8px; }
  .back-web {
    position: absolute; left: 0; right: 0; bottom: 30px;
    text-align: center;
    color: var(--white);
    font-size: 12px;
    letter-spacing: 3px;
  }
</style>
</head>
<body>
  <section class="card card-front" aria-label="Business card front">
    <div class="accent-strip"></div>
    <div class="front-brand">
      <span class="brand-name">VELRAN</span>
      <span class="brand-sub">GLOBAL COMPONENTS</span>
    </div>
    <div class="contact-panel">
      <p class="person-name">ALDEN ROSCOE</p>
      <p class="person-role">CEO/ Founder</p>
      <p class="address">17 Marlow Yard, Upper Heath<br>Warwick, CV31 8QL<br>United Kingdom</p>
      <ul class="contact-list">
        <li>
          <svg viewBox="0 0 12 12" aria-hidden="true"><path fill="currentColor" d="M2.4 0.6l1.9 2.1-1 1.3c.7 1.5 2 2.8 3.6 3.6l1.3-1 2.1 1.9-.9 1.8C5 10 1.6 6.6.6 3z"/></svg>
          555 014 2738
        </li>
        <li>
          <svg viewBox="0 0 12 12" aria-hidden="true"><rect x="3" y="0.5" width="6" height="11" rx="1" fill="none" stroke="currentColor"/><circle cx="6" cy="9.6" r=".7" fill="currentColor"/></svg>
          555 017 6491
        </li>
        <li>
          <svg viewBox="0 0 12 12" aria-hidden="true"><rect x="0.5" y="2" width="11" height="8" fill="none" stroke="currentColor"/><path d="M.5 2L6 6.5 11.5 2" fill="none" stroke="currentColor"/></svg>
          alden@velrancomponents-example.co.uk
        </li>
        <li>
          <svg viewBox="0 0 12 12" aria-hidden="true"><circle cx="6" cy="6" r="5.5" fill="none" stroke="currentColor"/><path d="M.5 6h11M6 .5c-2.5 3-2.5 8 0 11M6 .5c2.5 3 2.5 8 0 11" fill="none" stroke="currentColor" stroke-width=".8"/></svg>
          www.velrancomponents-example.co.uk
        </li>
      </ul>
    </div>
  </section>

  <section class="card card-back" aria-label="Business card back">
    <div class="back-brand">
      <span class="brand-name">VELRAN</span>
      <span class="brand-sub">GLOBAL COMPONENTS</span>
    </div>
    <p class="back-web">www.velrancomponents-example.co.uk</p>
  </section>
</body>
</html>
```